Flyer for spiritual retreat (yoga, meditation, reiki, raw food)

I would like a flyer to promote my upcoming retreat and a matching Facebook banner.

The name of the retreat is "OutBloom the Spirit" and the tagline is "retreat into you"

The activities in the retreat include daily meditation, ecstatic dance, spiritual development workshops on intuition, energy healing etc and a reiki session is included.

I would like a flyer designed to promote this, something that is editable as I will be running this multiple times and will need to adjust the flyer to add the dates etc each time.

edit: add that here will be fully catered raw food and juices, and that the retreat price includes all accomodation, meals and workshops.

Please contact me if you need further info. Please also visit my website www.marlavosk.com and www.pagenest.com/koruhaven to see my current events and promotions.

Thank you,

Marla

Reason: Hi all, thank you all for your submissions. Apologies as I am traveling and do not have much access to internet and will review your submissions and provide feedback as soon as possible. Kind regards, Marla.

Target Market(s)

People who like meditation, yoga, fans of tomas brenner and wendell marsh, those interested in personal and spiritual development.

Industry/Entity Type

Health And Wellness

Requirements
Must have
• Please put the included reiki session as as added bonus. Something like "BONUS 30 minute reiki healing session" in a little star/banner/something that stands out.
• Please emphasise the "light" part of OutBloom as I am going for a play on words between in the light and enlightenment.
• Please include placeholder text for place, location, time
• Placeholder for price
• My name (see attached file - can change colour to suit) and website (www.marlavosk.com)
Nice to have
• I prefer rounded designs, curves rather than block designs.
Should not have
• Koru Haven logo

```html
<!DOCTYPE html>
<html lang="en">
<head>
<meta charset="utf-8">
<title>OutBloom the Spirit – Retreat Into You</title>
<link rel="stylesheet" href="https://fonts.googleapis.com/css2?family=Roboto:ital,wght@0,300;0,400;0,700;0,900;1,900&family=Oswald:wght@400;500&display=swap">
<style>
  :root {
    --sky: #1ba3e0;
    --ink: #141414;
    --slate: #4a4a4c;
    --paper: #f1f1f3;
    --white: #ffffff;
    --footer: #2b2b2d;
    --badge-red: #e3232b;
    --badge-yellow: #ffe21a;
  }
  * { margin: 0; padding: 0; box-sizing: border-box; }
  html, body { width: 848px; height: 1200px; overflow: hidden; background: var(--paper); }
  .flyer {
    position: relative;
    width: 848px;
    height: 1200px;
    overflow: hidden;
    background: var(--paper);
    font-family: "Roboto", Arial, sans-serif;
  }
  .backdrop { position: absolute; inset: 0; }

  .host-name {
    position: absolute;
    left: 48px;
    top: 150px;
    font-weight: 300;
    font-size: 64px;
    color: var(--white);
    letter-spacing: 1px;
  }

  .bonus-badge {
    position: absolute;
    left: 78px;
    top: 640px;
    width: 214px;
    height: 214px;
    transform: rotate(-14deg);
  }
  .bonus-badge .burst {
    position: absolute;
    inset: 0;
    background: var(--badge-red);
    clip-path: polygon(100% 50%, 92.2% 58.4%, 96.2% 69.2%, 85.7% 73.9%, 85.4% 85.4%, 73.9% 85.7%, 69.2% 96.2%, 58.4% 92.2%, 50% 100%, 41.6% 92.2%, 30.8% 96.2%, 26.1% 85.7%, 14.6% 85.4%, 14.3% 73.9%, 3.8% 69.2%, 7.8% 58.4%, 0% 50%, 7.8% 41.6%, 3.8% 30.8%, 14.3% 26.1%, 14.6% 14.6%, 26.1% 14.3%, 30.8% 3.8%, 41.6% 7.8%, 50% 0%, 58.4% 7.8%, 69.2% 3.8%, 73.9% 14.3%, 85.4% 14.6%, 85.7% 26.1%, 96.2% 30.8%, 92.2% 41.6%);
  }
  .bonus-badge .copy {
    position: absolute;
    inset: 0;
    display: flex;
    flex-direction: column;
    align-items: center;
    justify-content: center;
    color: var(--white);
    font-weight: 900;
    line-height: 1;
    text-align: center;
  }
  .bonus-label { font-size: 30px; letter-spacing: 1px; }
  .bonus-length { display: flex; align-items: center; gap: 3px; margin: 2px 0; }
  .bonus-length .num { font-size: 62px; color: var(--badge-yellow); letter-spacing: -2px; }
  .bonus-length .unit { font-size: 18px; font-weight: 700; }
  .bonus-detail { font-size: 24px; font-weight: 700; line-height: 1.05; }

  .title { position: absolute; left: 0; top: 0; width: 848px; height: 1200px; font-size: inherit; }
  .title span { position: absolute; line-height: 1; white-space: nowrap; }
  .title .out { left: 636px; top: 628px; font-size: 82px; font-weight: 900; color: var(--sky); }
  .title .bloom { right: 18px; top: 688px; font-size: 150px; font-weight: 900; color: var(--sky); letter-spacing: -3px; }
  .title .the { left: 404px; top: 818px; font-size: 78px; font-weight: 400; color: var(--slate); }
  .title .spirit { right: 16px; top: 808px; font-size: 128px; font-weight: 700; color: var(--slate); letter-spacing: -2px; }

  .rule { position: absolute; height: 2px; background: var(--ink); }
  .rule-top { left: 360px; right: 0; top: 930px; }
  .rule-bottom { left: 150px; right: 0; top: 1000px; }

  .tagline {
    position: absolute;
    left: 128px;
    top: 936px;
    font-weight: 900;
    font-style: italic;
    font-size: 62px;
    line-height: 1;
    color: var(--ink);
    letter-spacing: 0.5px;
  }

  .activities {
    position: absolute;
    left: 0;
    right: 0;
    top: 1014px;
    text-align: center;
    font-family: "Oswald", "Arial Narrow", sans-serif;
    font-size: 31px;
    line-height: 36px;
    color: var(--ink);
    text-transform: uppercase;
  }

  .details {
    position: absolute;
    left: 0;
    right: 0;
    top: 1088px;
    text-align: center;
    font-family: "Oswald", "Arial Narrow", sans-serif;
    font-size: 17px;
    line-height: 21px;
    color: var(--slate);
    text-transform: uppercase;
    letter-spacing: 0.3px;
  }
  .details .when { color: var(--sky); font-weight: 500; }

  .footer {
    position: absolute;
    left: 0;
    right: 0;
    bottom: 0;
    height: 64px;
    background: var(--footer);
    display: flex;
    align-items: center;
    justify-content: space-between;
    padding: 0 24px 0 22px;
    color: var(--white);
    font-weight: 700;
    font-size: 21px;
    text-transform: uppercase;
  }
  .footer .contact { display: flex; align-items: center; gap: 10px; }
  .footer .dot { width: 16px; height: 16px; border-radius: 50%; background: var(--white); }
</style>
</head>
<body>
<div class="flyer">
  <svg class="backdrop" width="848" height="1200" viewBox="0 0 848 1200">
    <defs>
      <linearGradient id="meadow" x1="0" y1="0" x2="1" y2="1">
        <stop offset="0" stop-color="#5fc6c8"/>
        <stop offset="0.45" stop-color="#6aa86a"/>
        <stop offset="1" stop-color="#2f6a3a"/>
      </linearGradient>
    </defs>
    <rect role="img" aria-label="Photo: woman in a white top meditating cross-legged on grass in a sunlit green park" x="0" y="0" width="848" height="700" fill="url(#meadow)"/>

    <path d="M250 0 H848 V52 Q560 70 250 0 Z" fill="var(--white)"/>
    <path d="M290 28 Q560 92 848 52 V70 Q560 110 290 28 Z" fill="var(--ink)"/>
    <path d="M420 118 Q640 118 848 40 V66 Q640 150 420 118 Z" fill="var(--sky)"/>

    <path d="M0 690 Q360 560 848 600 V1200 H0 Z" fill="var(--paper)"/>
    <path d="M0 640 Q340 540 848 580 V600 Q360 560 0 676 Z" fill="var(--sky)"/>
    <path d="M0 676 Q360 560 848 600 V614 Q360 580 0 694 Z" fill="var(--ink)"/>
  </svg>

  <div class="host-name">Marla Vosk</div>

  <div class="bonus-badge">
    <div class="burst"></div>
    <div class="copy">
      <div class="bonus-label">BONUS</div>
      <div class="bonus-length"><span class="num">30</span><span class="unit">minute</span></div>
      <div class="bonus-detail">reiki<br>healing<br>session</div>
    </div>
  </div>

  <h1 class="title">
    <span class="out">Out</span>
    <span class="bloom">Bloom</span>
    <span class="the">the</span>
    <span class="spirit">Spirit</span>
  </h1>

  <div class="rule rule-top"></div>
  <p class="tagline">RETREAT INTO YOU</p>
  <div class="rule rule-bottom"></div>

  <p class="activities">Daily meditation, ecstatic dance,<br>spiritual development workshops on intuition</p>

  <p class="details">
    Fully catered raw food &amp; juices · Price includes all accommodation, meals &amp; workshops<br>
    <span class="when">Place: Venue name · Location: Town, Region · Time: 00:00 – 00:00 · Price: $000</span>
  </p>

  <footer class="footer">
    <div class="contact"><span class="dot"></span>www.marlavosk.com</div>
    <div class="contact"><span class="dot"></span>www.pagenest.com/koruhaven</div>
  </footer>
</div>
</body>
</html>
```